ELsewhen website redesign to provide information about experiential workshops, film work and other

We need a redesign of our website elsewhen.org. We conduct experiential workshops of discovery and transformation for individuals and organizations. We need the website to reflect the full extent of ELsewhen programs, and be an information hub for ELsewhen workshops and communities as they develop.

The attached documents contain information about the organization - it's brandbook, copy for web pages, a website layout and a couple of images.

The site is for individuals and companies looking to promote and be change to make a difference. It should be warm, welcoming, and create excitement around the concepts and the ability to discover a new way of being in the world. We are about creating communities around the globe who will embody play, freedom, curiosity and expanded possibilities. We are creating a space for this to happen, both physically (workshops) and online.

We will be on either a SquareSpace, but mos tlikely a Weebly plaform.

Please look at the current site at www.elsewhen.org

Target Market(s)

Initially, are target market will be baby boomers, but will expand to include millennials and students.

Coding

Coded - Design and coding required

Number of Pages Required

5+ page

Requirements
Must have
• The colors, logo and fonts from the brand book.
Nice to have
• Complimentary use of brand colors to create an attractive presentation and energy

```html
<!DOCTYPE html>
<html lang="en">
<head>
<meta charset="utf-8">
<title>ELsewhen</title>
<link href="https://fonts.googleapis.com/css2?family=Hind:wght@400;500;600;700&display=swap" rel="stylesheet">
<style>
:root{
  --orange:#f47a3d;
  --amber:#f4b350;
  --ink:#1f1f1f;
  --muted:#8a8a8a;
  --panel:#f4f4f4;
  --slate:#4a4a4a;
  --white:#ffffff;
}
*{margin:0;padding:0;box-sizing:border-box}
html,body{width:686px;height:1200px;overflow:hidden;background:var(--white)}
body{position:relative;font-family:"Hind",Arial,sans-serif;color:var(--ink)}
.abs{position:absolute}
.hero{left:0;top:0;width:686px;height:339px;background:linear-gradient(100deg,#6f6f6f 0%,#5a5a5a 45%,#3d4038 100%)}
.hero-shade{left:0;top:0;width:686px;height:339px}
.brand{left:92px;top:27px;display:flex;align-items:center;gap:6px;color:var(--white);font-weight:700;font-size:17px;letter-spacing:2px}
.brand-mark{width:10px;height:10px;background:var(--white)}
.banner{left:92px;top:106px}
.banner-text{color:var(--white);font-weight:600;font-size:18px;line-height:24px;text-transform:uppercase;white-space:nowrap}
.banner-left{left:120px;top:146px;width:215px;text-align:right}
.banner-right{left:353px;top:134px;width:200px}
.banner-right span{display:block}
.dash{width:15px;height:3px;background:var(--orange)}
.intro-title{left:0;top:391px;width:686px;text-align:center;font-size:9.5px;font-weight:600}
.values{left:84px;top:428px;width:520px;display:flex;justify-content:space-between}
.value{width:96px;text-align:center;font-size:6.5px;font-weight:600;line-height:8px}
.value svg{display:block;margin:0 auto 10px}
.vision{left:0;top:550px;width:686px;height:206px;background:var(--panel)}
.vision-photo{left:0;top:550px}
.h2{font-size:14px;font-weight:600}
.copy{font-size:5.8px;line-height:10.3px;color:var(--muted);white-space:nowrap}
.btn{left:223px;top:694px}
.btn-label{left:223px;top:701px;width:76px;text-align:center;color:var(--white);font-size:6px;font-weight:700}
.slate{left:0;top:756px}
.work-title{left:0;top:805px;width:686px;text-align:center}
.work-copy{left:0;top:836px;width:686px;text-align:center}
.life-line{left:0;top:886px;width:686px;text-align:center;font-size:9px;font-weight:600}
.life-line span{color:var(--muted);font-weight:500}
.moves{left:92px;top:915px}
.move-label{top:979px;width:100px;text-align:center;font-size:7px;font-weight:600}
.lower{left:0;top:1047px;width:686px;height:132px;background:var(--panel)}
.col-title{font-size:9px;font-weight:600}
.footer{left:0;top:1179px;width:686px;height:21px;background:var(--orange)}
.copyright{left:92px;top:1187px;font-size:5px;color:var(--white)}
.social{left:524px;top:1186px;display:flex;gap:13px}
.social i{display:block;width:7px;height:7px;border-radius:50%;border:1px solid #3a2318}
</style>
</head>
<body>

<div class="abs hero" role="img" aria-label="Photo of a community procession with costumed performers in front of a wooden barn covered in printed artwork"></div>
<svg class="abs hero-shade" width="686" height="339" aria-hidden="true">
  <polygon points="0,0 380,0 280,339 0,339" fill="#ffffff" opacity="0.08"/>
</svg>
<div class="abs brand"><span class="brand-mark"></span>ELSEWHEN</div>

<svg class="abs banner" width="502" height="128" aria-hidden="true">
  <polygon points="51,0 282,0 229,128 0,128" fill="var(--amber)"/>
  <polygon points="282,0 502,0 451,128 229,128" fill="var(--orange)"/>
</svg>
<div class="abs banner-text banner-left">What world do<br>we want to live in?</div>
<div class="abs banner-text banner-right"><span style="padding-left:19px">What kind of</span><span style="padding-left:10px">life do you want</span><span>to create?</span></div>

<div class="abs dash" style="left:335px;top:379px"></div>
<div class="abs intro-title">Discover an Opportunity to Live a More Dynamic and Meaningful Life</div>

<div class="abs values">
  <div class="value"><svg width="76" height="52"><polygon points="20,0 76,0 56,52 0,52" fill="var(--panel)"/><rect x="30" y="16" width="16" height="16" fill="var(--orange)"/></svg>Moves Energy</div>
  <div class="value"><svg width="76" height="52"><polygon points="20,0 76,0 56,52 0,52" fill="var(--panel)"/><rect x="30" y="16" width="16" height="16" fill="var(--ink)"/></svg>Creates Opportunities<br>for Connecting</div>
  <div class="value"><svg width="76" height="52"><polygon points="20,0 76,0 56,52 0,52" fill="var(--panel)"/><rect x="30" y="16" width="16" height="16" fill="var(--ink)"/></svg>Supports Conscious<br>Evolution</div>
  <div class="value"><svg width="76" height="52"><polygon points="20,0 76,0 56,52 0,52" fill="var(--panel)"/><rect x="30" y="16" width="16" height="16" fill="var(--ink)"/></svg>Deepens Experience<br>of Life</div>
  <div class="value"><svg width="76" height="52"><polygon points="20,0 76,0 56,52 0,52" fill="var(--panel)"/><rect x="30" y="16" width="16" height="16" fill="var(--ink)"/></svg>Provides Opportunities for<br>Collaboration &amp; Creation</div>
</div>

<div class="abs vision"></div>
<svg class="abs vision-photo" width="200" height="206" role="img" aria-label="Photo of workshop participants seated in a circle on the floor of a wood-panelled room">
  <defs><linearGradient id="room" x1="0" y1="0" x2="1" y2="1"><stop offset="0" stop-color="#5d4a3a"/><stop offset="1" stop-color="#8a7a6c"/></linearGradient></defs>
  <polygon points="0,0 200,0 124,206 0,206" fill="url(#room)"/>
</svg>
<div class="abs dash" style="left:223px;top:590px"></div>
<div class="abs h2" style="left:223px;top:598px">Elsewhen Vision</div>
<p class="abs copy" style="left:223px;top:629px">We envision a world in which all people and communities can challenge and break free from stories that no longer serve us.<br>We believe that solutions to contemporary challenges will emerge from a place of curiosity, love and connection.</p>
<p class="abs copy" style="left:223px;top:660px">Through inspiration, conscious reflection, and collaboration, we take responsibility for the world we are manifesting, and we<br>can discover and create new possibilities for the lives and the society we desire to build.</p>
<svg class="abs btn" width="76" height="23" aria-hidden="true"><polygon points="8,0 76,0 68,23 0,23" fill="var(--orange)"/></svg>
<div class="abs btn-label">READ MORE</div>

<svg class="abs slate" width="124" height="320" aria-hidden="true"><polygon points="0,0 124,0 0,320" fill="var(--slate)"/></svg>
<div class="abs dash" style="left:335px;top:795px"></div>
<div class="abs h2 work-title">What We Do</div>
<p class="abs copy work-copy">Elsewhen Life is a workshop designed to re-engage you with life. Through interactive exercises and personal exploration, you are taken on a journey<br>that ultimately leaves you experiencing life as a Creator. You will learn to see beliefs and patterns that hold you back in work and relationships as well<br>as a path to transforming the story of your life.</p>
<div class="abs life-line">Elsewhen Life <span>is a 2-3 day workshop experienced in</span> 5 movements:</div>

<svg class="abs moves" width="502" height="85" aria-hidden="true">
  <rect width="502" height="85" fill="var(--panel)"/>
  <polyline points="296,0 314,42.5 296,85" fill="none" stroke="#ffffff" stroke-width="1.5"/>
  <polyline points="396,0 414,42.5 396,85" fill="none" stroke="#ffffff" stroke-width="1.5"/>
  <polygon points="99,0 196,0 215,42.5 196,85 99,85 118,42.5" fill="var(--orange)"/>
  <g fill="none" stroke="var(--orange)" stroke-width="1.6">
    <circle cx="53" cy="33" r="10"/>
    <circle cx="255" cy="33" r="10"/>
    <circle cx="354" cy="33" r="10"/>
    <circle cx="456" cy="33" r="10"/>
  </g>
  <circle cx="158" cy="33" r="10" fill="none" stroke="#ffffff" stroke-width="1.6"/>
</svg>
<div class="abs move-label" style="left:95px">Curiosity</div>
<div class="abs move-label" style="left:199px;color:#ffffff">Awareness</div>
<div class="abs move-label" style="left:298px">Owning Your Creation</div>
<div class="abs move-label" style="left:396px">Amazement</div>
<div class="abs move-label" style="left:498px">Interconnection</div>

<div class="abs lower"></div>
<div class="abs dash" style="left:92px;top:1087px"></div>
<div class="abs col-title" style="left:92px;top:1097px">Breaking the Quiet</div>
<p class="abs copy" style="left:92px;top:1118px">The Breaking the Quiet workshop—an extension of the documentary of the same name—is<br>an experiential process to transform participants into disturbers of the status quo within<br>themselves, to enhance their relationships with others, and to change the environments in<br>which they exist—and ultimately society—for the better.</p>
<div class="abs dash" style="left:402px;top:1087px"></div>
<div class="abs col-title" style="left:402px;top:1097px">In Your Community</div>
<p class="abs copy" style="left:402px;top:1118px">Bring Elsewhen or the Breaking the Quiet workshop to your<br>community. We would love to hear from you. Please fill out the<br>brief form here (link to In Your Community page</p>

<div class="abs footer"></div>
<div class="abs copyright">© Copyright 2018 ELsewhen, All Rights Reserved.</div>
<div class="abs social" aria-label="Social links"><i></i><i></i><i></i><i></i></div>

</body>
</html>
```